Commercial Loan Originator Business Card (CHANGE COLORS SCHEME)

CHANGE COLOR SCHEME - SAME DESIGN

Name Marlene Agate
Title Commercial Loan Originator
Office (800) 417-2906 x68
Direct (240) 615-2043
Email freshgreens4life@quillbox.example

Name Dale Morrow
Office (800) 417-2906 x70
Direct (410) 392-5184
Email d.morthehomeguy@quillbox.example

Name Leonard Vasko
Office (800) 417-2906 x71
Direct (215) 463-0712
Email l.vasko41@quillbox.example

Name Gwen Halsey
Office (800) 417-2906 x
Direct (202) 548-1370
Email ghalsey63@quillbox.example

Name Mirna Ashby
Office (800) 417-2906 x72
Direct (240) 871-4526
Email tristatehomelending@quillbox.example

```html
<!DOCTYPE html>
<html lang="en">
<head>
<meta charset="utf-8">
<title>Dale Morrow – Business Card</title>
<link rel="stylesheet" href="https://fonts.googleapis.com/css2?family=Great+Vibes&family=Cormorant+Garamond:wght@500&family=Poppins:wght@300;400;600&display=swap">
<style>
  :root {
    --page: #ffffff;
    --card-base: #0d1a2e;
    --card-mid: #1d3557;
    --card-glow: #5f7fa8;
    --pill: #0a1424;
    --row: #08111f;
    --row-line: #1f3352;
    --icon-bg: #16294a;
    --icon-ring: #c9a85c;
    --accent: #d8b86a;
    --ink: #ffffff;
    --ink-soft: #dfe6f0;
    --photo-dark: #12233d;
    --photo-light: #4d6a91;
  }
  * { box-sizing: border-box; margin: 0; padding: 0; }
  html, body { width: 1010px; height: 1200px; overflow: hidden; background: var(--page); }
  .card {
    position: absolute; left: 108px; width: 794px; height: 454px;
    overflow: hidden; color: var(--ink);
    background: radial-gradient(ellipse 420px 360px at 82% 0%, var(--card-glow) 0%, var(--card-mid) 45%, var(--card-base) 100%);
    box-shadow: 10px 14px 18px rgba(0,0,0,.35);
  }
  .card--front { top: 113px; }
  .card--back { top: 633px; }

  .name-block { position: absolute; text-align: center; }
  .name-first {
    display: block; font-family: "Great Vibes", cursive; font-size: 112px; line-height: 1;
    color: var(--accent); text-shadow: 0 0 6px rgba(0,0,0,.7);
  }
  .name-last {
    display: block; font-family: "Cormorant Garamond", serif; font-weight: 500;
    font-size: 54px; letter-spacing: 2px; line-height: 1; margin-top: -26px;
  }
  .job-title {
    display: block; font-family: "Poppins", sans-serif; font-weight: 300;
    font-size: 18px; color: var(--ink-soft); margin-top: 6px;
  }

  .pill {
    position: absolute; left: 40px; top: 89px; width: 800px; height: 276px;
    border-radius: 138px 0 0 138px; background: var(--pill); opacity: .85;
  }
  .card--front .name-block { left: 90px; width: 380px; top: 142px; }
  .portrait {
    position: absolute; left: 431px; top: 35px; width: 343px; height: 419px;
    border-radius: 140px 140px 0 0;
    background: linear-gradient(180deg, var(--photo-light) 0%, var(--photo-dark) 100%);
  }

  .card--back .name-block { left: 0; width: 794px; top: 34px; }
  .card--back .name-first { font-size: 96px; }
  .card--back .name-last { font-size: 48px; margin-top: -20px; }
  .card--back .job-title { font-size: 16px; margin-top: 2px; }

  .contact-icons {
    position: absolute; top: 208px; left: 0; width: 794px;
    display: flex; justify-content: center; gap: 8px;
  }
  .contact-icon {
    width: 34px; height: 34px; border-radius: 50%;
    background: var(--icon-bg); border: 1px solid var(--icon-ring);
    display: flex; align-items: center; justify-content: center;
  }
  .contact-icon svg { width: 16px; height: 16px; fill: var(--accent); }

  .contact-list { position: absolute; left: 36px; top: 239px; width: 723px; list-style: none; }
  .contact-row {
    height: 57px; margin-bottom: 3px; background: var(--row);
    border-bottom: 1px solid var(--row-line);
    display: flex; align-items: center; justify-content: center;
    font-family: "Poppins", sans-serif; font-size: 18px; font-weight: 400;
  }
  .contact-row strong { font-weight: 600; margin-right: 6px; }
  .contact-row--email { font-weight: 600; }
</style>
</head>
<body>

<section class="card card--front">
  <div class="pill"></div>
  <div class="name-block">
    <span class="name-first">Dale</span>
    <span class="name-last">MORROW</span>
    <span class="job-title">Commercial Loan Originator</span>
  </div>
  <div class="portrait" role="img" aria-label="Portrait of Dale Morrow in a suit jacket"></div>
</section>

<section class="card card--back">
  <div class="name-block">
    <span class="name-first">Dale</span>
    <span class="name-last">MORROW</span>
    <span class="job-title">Commercial Loan Originator</span>
  </div>

  <div class="contact-icons">
    <span class="contact-icon" aria-label="Office">
      <svg viewBox="0 0 16 16"><path d="M2 15V4h4V1h7v14h-3v-3H8v3z M8 3h1v1H8z M10 3h1v1h-1z M8 5h1v1H8z M10 5h1v1h-1z M8 7h1v1H8z M10 7h1v1h-1z M3 6h1v1H3z M3 8h1v1H3z M3 10h1v1H3z" fill-rule="evenodd"/></svg>
    </span>
    <span class="contact-icon" aria-label="Phone">
      <svg viewBox="0 0 16 16"><path d="M3.5 1.5l2.2 2.3-1 1.7c.8 1.9 2.1 3.2 4 4l1.6-1 2.3 2.2-1.3 2.3C6.8 12.6 3.3 9.2 1.3 4z"/></svg>
    </span>
    <span class="contact-icon" aria-label="Email">
      <svg viewBox="0 0 16 16"><path d="M1 3h14v10H1z M2 4.2v.3l6 4.2 6-4.2v-.3z" fill-rule="evenodd"/></svg>
    </span>
  </div>

  <ul class="contact-list">
    <li class="contact-row"><strong>Office</strong>(800) 417-2906 x70</li>
    <li class="contact-row"><strong>Direct</strong>(410) 392-5184</li>
    <li class="contact-row contact-row--email">d.morthehomeguy@quillbox.example</li>
  </ul>
</section>

</body>
</html>
```